A business card design for a dental office. We have Two doctors working here. We practice general de

I already have a logo designed for the office with the name and a slogan.
Now I need to create design for a business card using the same logo.
Details Needed on the front side of the card are :
Bernard K. Oswin, DDS
Gerald M Fenwick, DDS
418 Birch Lane
Portland, CT 00000
Phone : 555 019 4831
Fax : 555 019 4832
Website : WWW.BrightmoorToothHaven.Com
Office hours by appointment
On the back side of the card need :
Appointment
Date....................Time...................
With....................................
If unable to keep your appointment, please give 24-48 hours notice in order to avoid broken appointment fee.

Industry/Entity Type

Dental Clinic

Contact Information for Business Card

Bernard K. Oswin, DDS
Gerald M Fenwick, DDS
418 Birch Lane
Portland, CT 00000
Phone : 555 019 4831
Fax : 555 019 4832
Appointment

Requirements
Must have
• Keep the Name and slogan on the logo on the front of the card. You can move them around the Logo and Name/Slogan of business (Oswin Family Dentistry/Caring for every family smile) as you wish to get a feel of the design.
• Bernard K. Oswin, DDS
• Gerald M Fenwick, DDS
• 418 Birch Lane
• Portland, CT 00000
• Phone : 555 019 4831
• Fax : 555 019 4832
• WWW.BrightmoorToothHaven.Com
• Keep these three groups above as they are together now in different areas of the front side.
• On the back side of the card need :
• Appointment
• Date....................Time...................
• With....................................
• If unable to keep your appointment, please give 24-48 hours notice in order to avoid broken appointment fee.

```html
<!DOCTYPE html>
<html lang="en">
<head>
<meta charset="utf-8">
<title>Oswin Family Dentistry – Business Card</title>
<link rel="stylesheet" href="https://fonts.googleapis.com/css2?family=Source+Sans+3:ital,wght@0,400;0,600;0,700;1,600&display=swap">
<style>
  :root {
    --stage-top: #2b2b2b;
    --stage-bottom: #050505;
    --card-front: #f3f3f3;
    --card-back: #ffffff;
    --brand-blue: #1b4f9c;
    --slogan-red: #e0303a;
    --mark-tint: #cfe3f3;
    --ink: #1c1c1c;
  }
  * { margin: 0; padding: 0; box-sizing: border-box; }
  html, body { width: 1200px; height: 900px; overflow: hidden; }
  body {
    background: linear-gradient(180deg, var(--stage-top) 0%, #1a1a1a 55%, var(--stage-bottom) 100%);
    font-family: "Source Sans 3", Arial, sans-serif;
    position: relative;
  }
  .card {
    position: absolute;
    top: 184px;
    height: 490px;
    border-radius: 12px;
    text-align: center;
    color: var(--ink);
  }
  .card-front { left: 299px; width: 301px; background: var(--card-front); }
  .card-back  { left: 645px; width: 305px; background: var(--card-back); }

  .brand-mark {
    position: absolute;
    left: 50%;
    transform: translateX(-50%);
    border-radius: 50%;
    background: var(--mark-tint);
  }
  .card-front .brand-mark { top: 38px; width: 80px; height: 80px; }
  .card-back .brand-mark  { top: 30px; width: 140px; height: 140px; }

  .brand-name {
    position: absolute; left: 0; right: 0;
    color: var(--brand-blue);
    font-weight: 600;
    letter-spacing: 1px;
    text-transform: uppercase;
  }
  .card-front .brand-name { top: 142px; font-size: 16px; }
  .card-back .brand-name  { top: 182px; font-size: 15px; }

  .tagline {
    position: absolute; left: 0; right: 0; top: 164px;
    display: flex; align-items: center; justify-content: center; gap: 6px;
    color: var(--slogan-red);
    font-size: 7.5px;
    letter-spacing: 0.8px;
    text-transform: uppercase;
  }
  .tagline::before, .tagline::after {
    content: ""; width: 18px; height: 1px; background: var(--slogan-red);
  }

  .doctors {
    position: absolute; left: 0; right: 0; top: 232px;
    color: var(--brand-blue);
    font-size: 20px; font-weight: 600; line-height: 21px;
  }
  .address {
    position: absolute; left: 0; right: 0; top: 300px;
    font-style: normal;
    font-size: 14px; line-height: 20px;
  }
  .contact-list {
    position: absolute; left: 0; right: 0; top: 366px;
    list-style: none; font-size: 14px; line-height: 20.5px;
  }
  .contact-list svg { width: 10px; height: 10px; fill: var(--brand-blue); margin-right: 4px; vertical-align: -1px; }
  .office-hours {
    position: absolute; left: 0; right: 0; top: 438px;
    color: var(--brand-blue);
    font-size: 14px; font-style: italic; font-weight: 600;
  }

  .appointment-title {
    position: absolute; left: 0; right: 0; top: 222px;
    color: var(--brand-blue);
    font-size: 20px; font-weight: 600; letter-spacing: 0.5px;
  }
  .appointment-fields {
    position: absolute; left: 40px; top: 286px;
    text-align: left; color: var(--brand-blue);
    font-size: 16px; font-weight: 600;
  }
  .field-row { display: flex; align-items: baseline; height: 39px; }
  .field-line { display: inline-block; border-bottom: 2px dotted var(--ink); margin: 0 10px 0 12px; }
  .notice {
    position: absolute; left: 0; right: 0; top: 388px;
    font-size: 14px; font-weight: 700; line-height: 18.5px;
  }
</style>
</head>
<body>

<section class="card card-front" aria-label="Business card front">
  <div class="brand-mark"></div>
  <div class="brand-name">Oswin Family Dentistry</div>
  <div class="tagline">Caring for every family smile</div>

  <div class="doctors">
    <p>Bernard K. Oswin, DDS</p>
    <p>Gerald M Fenwick, DDS</p>
  </div>

  <address class="address">
    <p>418 Birch Lane</p>
    <p>Portland, CT 00000</p>
  </address>

  <ul class="contact-list">
    <li><svg viewBox="0 0 10 10" aria-label="Phone"><path d="M2 0.5 L3.6 2.6 L2.8 3.6 Q3.8 5.8 6.2 7.2 L7.2 6.4 L9.5 8 L8.4 9.6 Q4.5 9.4 1.6 6 Q0 3.8 0.5 1.6 Z"/></svg>555 019 4831</li>
    <li><svg viewBox="0 0 10 10" aria-label="Fax"><rect x="2.5" y="0.5" width="5" height="3"/><rect x="0.5" y="3.5" width="9" height="5.5" rx="1"/><rect x="2.5" y="6" width="5" height="4" fill="#ffffff"/></svg>555 019 4832</li>
    <li><svg viewBox="0 0 10 10" aria-label="Website"><circle cx="5" cy="5" r="4.7"/></svg>WWW.BrightmoorToothHaven.Com</li>
  </ul>

  <p class="office-hours">Office hours by appointment</p>
</section>

<section class="card card-back" aria-label="Business card back">
  <div class="brand-mark"></div>
  <div class="brand-name">Oswin Family Dentistry</div>

  <h2 class="appointment-title">APPOINTMENT</h2>

  <div class="appointment-fields">
    <div class="field-row">Date<span class="field-line" style="width:54px"></span>Time<span class="field-line" style="width:66px"></span></div>
    <div class="field-row">With<span class="field-line" style="width:178px"></span></div>
  </div>

  <p class="notice">If unable to keep your appointment,<br>please give 24-48 hours notice in order<br>to avoid broken appointment fee.</p>
</section>

</body>
</html>
```